Computer Consulting Brochure

Computer Consulting services for schools, small businesses, local governments and medical offices. We design networks, security, monitoring, applications for these environments.
Updates
Project Deadline Extended Reason: I provided a condensed document so as not to overwhelm designers. This document covers only pertinent info that can be further condensed if necessary for physical size constraints. Added Friday, April 7, 2017
Target Market(s)
Schools, Small Businesses, Medical Offices, Local Governments. 4 brochures that are identical except for a section that specifically describes the 4 markets.
Industry/Entity Type
Computer
Colors
Designer to choose colors to be used in the design.
Look and feel
Each slider illustrates characteristics of the customer's brand and the style your logo design should communicate.

```html
<!DOCTYPE html>
<html lang="en">
<head>
<meta charset="utf-8">
<title>NorthBridge IT Consulting Brochure</title>
<link href="https://fonts.googleapis.com/css2?family=Barlow+Condensed:wght@300;400;500;600&display=swap" rel="stylesheet">
<style>
:root{
  --bg:#e8e5e0;
  --paper:#ffffff;
  --teal:#1fa3c4;
  --teal-dark:#1389ad;
  --teal-pale:#dff1f6;
  --orange:#f3a41c;
  --orange-light:#f7c23a;
  --yellow-pale:#fbf1cf;
  --ink:#4a4a4a;
  --grey:#8a8f94;
  --white:#ffffff;
}
*{margin:0;padding:0;box-sizing:border-box}
html,body{width:1200px;height:1200px;overflow:hidden;background:var(--bg)}
body{font-family:"Barlow Condensed",sans-serif;color:var(--ink);position:relative}
.spread{position:absolute;left:220px;width:760px;height:580px;background:var(--paper);box-shadow:0 2px 10px rgba(0,0,0,.18);overflow:hidden}
.spread.outside{top:12px}
.spread.inside{top:604px}
.panel{position:absolute;top:0;width:253.33px;height:580px;overflow:hidden}
.p1{left:0}.p2{left:253.33px}.p3{left:506.66px}
h2{font-weight:600;color:var(--teal);font-size:19px;letter-spacing:.2px;line-height:1}
.lead{color:var(--teal);font-weight:600;font-size:10px;line-height:1.15;margin:4px 0 6px}
p,li{font-weight:300;font-size:7.4px;line-height:1.32}
p{margin-bottom:5px}
ul.bullets{list-style:none}
ul.bullets li{position:relative;padding-left:9px;margin-bottom:4px}
ul.bullets li::before{content:"";position:absolute;left:0;top:2px;width:5px;height:5px;background:var(--teal)}
.text{position:absolute;left:13px;right:13px;top:14px}
.photo{position:absolute}
/* outside */
.laptop-photo{left:0;right:0;bottom:0;height:120px;background:linear-gradient(180deg,rgba(255,255,255,1) 0%,#c9ced3 45%,#8e969e 100%)}
.building-photo{left:0;right:0;top:0;height:275px;background:linear-gradient(160deg,#f4f5f6 20%,#cfd4d8 55%,#9aa3aa 100%)}
.building-photo.faint{opacity:.35}
.solutions{position:absolute;left:0;right:0;top:275px;bottom:0;background:linear-gradient(180deg,var(--teal) 0%,#4fb8d1 100%);padding:22px 12px 0;color:var(--white);text-align:center}
.solutions h3{font-weight:500;font-size:15px;line-height:1.28;letter-spacing:.2px}
.contact{position:absolute;left:22px;bottom:12px;list-style:none}
.contact li{display:flex;align-items:center;gap:8px;font-size:9px;font-weight:400;color:var(--white);margin-top:3px}
.contact svg{width:10px;height:10px;flex:none}
.brand{position:absolute;top:12px;right:16px;font-size:20px;font-weight:300;color:var(--grey);display:flex;align-items:center;gap:6px}
.brand i{display:block;width:6px;height:6px;background:var(--teal)}
.cover-band{position:absolute;left:0;right:0;top:275px;bottom:0;background:linear-gradient(180deg,var(--orange-light) 0%,var(--orange) 100%);padding:18px 14px 0;text-align:right;color:var(--white)}
.cover-band h1{font-weight:500;font-size:30px;line-height:1.03;letter-spacing:.3px}
.cover-band .tag{font-weight:500;font-size:7.8px;line-height:1.15;margin-top:10px}
/* inside */
.band{position:absolute;top:0;height:72px}
.band.teal{left:0;width:506.66px;background:linear-gradient(90deg,#5bbcd6,var(--teal))}
.band.orange{left:506.66px;width:253.34px;background:linear-gradient(90deg,var(--orange),var(--orange-light))}
.band h2{color:var(--white)}
.why{position:absolute;left:18px;top:22px;font-size:34px}
.what{position:absolute;left:14px;top:14px;font-size:17px;line-height:1.05}
.why-left{position:absolute;left:0;top:72px;width:230px;height:300px;background:linear-gradient(180deg,var(--teal-pale),#c6e6ef)}
.students-photo{left:0;width:506.66px;bottom:0;height:210px;background:linear-gradient(180deg,rgba(255,255,255,0) 0%,#b9d7e2 35%,#8db0c2 100%)}
.col-a{position:absolute;left:18px;width:200px;top:86px}
.col-a .lead{margin-top:0}
.col-b{position:absolute;left:236px;width:200px;top:86px}
.what-col{position:absolute;left:506.66px;top:72px;width:253.34px;bottom:0;background:linear-gradient(180deg,#fffdf6,var(--yellow-pale))}
.what-col .inner{padding:12px 14px}
.what-col .lead{color:var(--orange);margin:6px 0 4px}
.what-col ul.bullets li::before{background:var(--orange)}
.what-col ul.bullets li{margin-bottom:3px}
</style>
</head>
<body>

<section class="spread outside">
  <article class="panel p1">
    <div class="text">
      <h2>AUTOMOBILE DEALERSHIPS</h2>
      <p class="lead">We can install a secure wireless system that covers the entire dealership and lots.</p>
      <ul class="bullets">
        <li>We can install a system that enables your salespeople to be much more productive and successful.</li>
        <li>We equip SlatePads and tablets to access your database of inventory and then present the data through our presentation app.</li>
      </ul>
      <p>Today your salespeople might be carrying sheets of paper as they walk through the sales lot with prospective customers and then fumble through them to obtain limited information about the model that the customer expresses an interest in. Instead, your salespeople can now walk with a SlatePad; no paper based system or relying on memory. Instantly they can access data about every model. Proprietary information can be displayed about the car. These items might be minimum sales price, desired sales price, the specific salesperson daily or monthly goals (and current numbers).</p>
      <p>Another possibility would be the display of potential sales incentives or bonuses the salesperson could earn on this model. The salesperson could also instantly access pertinent information about that particular model and associated options. This instantly allows the salesperson to push particulars that the customer might already have expressed an interest in (horsepower, mpg, type of drivetrain, etc.).</p>
      <p>There could be notes that the sales manager had entered about specific cars being pushed that day. The salesperson could instantly text the sales manager with specifics if the customer was close to purchasing instead of saying "Let's go back to my office and let me check with my manager", thereby greatly expediting the entire sales process and more likely closing the deal by eliminating those moments of hesitation or loss of enthusiasm by the customer.</p>
    </div>
    <div class="photo laptop-photo" role="img" aria-label="Photo of hands typing on a laptop keyboard"></div>
  </article>

  <article class="panel p2">
    <div class="photo building-photo faint" role="img" aria-label="Faint photo of a glass office tower"></div>
    <div class="text">
      <h2>RECENT PROJECTS</h2>
      <ul class="bullets" style="margin-top:8px">
        <li>Resolved a major problem at Harbor State University for one of their computer clusters used in their research department.</li>
        <li>Participated in the State of RI twenty million dollar project to upgrade all school environments to provide connectivity for every student on high speed wireless. (1:1 computing)</li>
        <li>Created a Lynex implementation in a large commercial environment. Designed a Lynex mail server running on the Nimbus cloud for hundreds of users.</li>
        <li>Provided 24x7 monitoring and support for a large boarding school. Implemented an enterprise wireless LAN for a large campus, a campus wide security camera system and a SlatePad/Orchard mobile device management system.</li>
        <li>Created a Directory Services domain and related security for a newly constructed medical office. Connected an ultrasound machine to the IT network and enabled external authorized doctors to securely connect to the server to view ultrasound recordings.</li>
      </ul>
    </div>
    <div class="solutions">
      <h3>OUR SOLUTIONS FOR SCHOOLS, MEDICAL/DENTAL, SMALL BUSINESSES AND AUTO DEALERSHIPS ARE COST EFFECTIVE BECAUSE THEY ARE CUSTOMIZED SPECIFICALLY FOR YOUR ENVIRONMENT. YOUR TYPE OF BUSINESS AND END USERS ARE CRITICAL FACTORS THAT SHOULD BE THE INFLUENCING DESIGN PARAMETERS</h3>
      <ul class="contact">
        <li><svg viewBox="0 0 10 10"><circle cx="5" cy="5" r="5" fill="#fff"/><rect x="2.5" y="3" width="5" height="3.5" fill="none" stroke="#1fa3c4" stroke-width="1"/></svg>www.northbridge-it.com</li>
        <li><svg viewBox="0 0 10 10"><circle cx="5" cy="5" r="5" fill="#fff"/><path d="M2.5 3.2h5v3.6h-5zM2.5 3.2l2.5 2 2.5-2" fill="none" stroke="#1fa3c4" stroke-width=".9"/></svg>hello@northbridge-it.com</li>
        <li><svg viewBox="0 0 10 10"><circle cx="5" cy="5" r="5" fill="#fff"/><path d="M3.3 2.6c.6 0 1 1.2 1 1.5s-.5.5-.4.8c.3.7.7 1.1 1.3 1.3.3.1.5-.4.8-.4s1.4.4 1.4 1c0 .4-.6.8-1.2.8-2 0-3.9-1.9-3.9-3.9 0-.6.5-1.1 1-1.1z" fill="#1fa3c4"/></svg>401-555-0142</li>
        <li><svg viewBox="0 0 10 10"><circle cx="5" cy="5" r="5" fill="#fff"/><path d="M5 8.3S3 5.9 3 4.4a2 2 0 0 1 4 0C7 5.9 5 8.3 5 8.3z" fill="#1fa3c4"/><circle cx="5" cy="4.4" r=".7" fill="#fff"/></svg>18 Mill Rd #204 Ashford, RI 02899-0204</li>
      </ul>
    </div>
  </article>

  <article class="panel p3">
    <div class="photo building-photo" role="img" aria-label="Photo looking up at a glass office tower"></div>
    <div class="brand"><i></i>NorthBridge</div>
    <div class="cover-band">
      <h1>DESIGN,<br>INSTALLATION &amp;<br>MANAGEMENT<br>OF COMPUTING<br>ENVIRONMENTS</h1>
      <p class="tag">WE CAN MONITOR(24X7), DESIGN+<br>INSTALL OR MODIFY</p>
      <p class="tag" style="margin-top:5px">IT ENVIRONMENTS CUSTOMIZED FOR SCHOOLS,<br>MEDICAL/DENTAL, SMALL BUSINESSES AND AUTO<br>DEALERSHIPS</p>
      <p class="tag" style="margin-top:5px">SECURITY CAMERA MONITORING SYSTEMS<br>ECONOMICALLY INTEGRATED INTO THE IT<br>ENVIRONMENT</p>
    </div>
  </article>
</section>

<section class="spread inside">
  <div class="band teal"><h2 class="why">WHY OUTSOURCE?</h2></div>
  <div class="band orange"><h2 class="what">WHAT WE DO<br>FOR ALL TYPES OF IT<br>ENVIRONMENTS</h2></div>
  <div class="why-left"></div>
  <div class="photo students-photo" role="img" aria-label="Photo of students working at rows of computers in a lab"></div>

  <div class="col-a">
    <p class="lead">We specialized in IT support at a scale tailored to your exact requirements</p>
    <p>A direct, dedicated IT staff will have either idle time during periods of stability or inadequate resources for those times when problems occur simultaneously.</p>
    <p>By outsourcing to NorthBridge your business will always have the ideal level of support, and therefore never overpay nor be insufficiently prepared to deal with sudden problems that can overwhelm insufficient numbers of staff.</p>
    <p>Because funds are allocated efficiently your business can now afford to capitalize on the most current technology and benefit from all features offered by these newest features.</p>
  </div>
  <div class="col-b">
    <p>Outsourcing is the better economical choice; there are no overtime hours, paid vacations, morale problems, costs associated with health care and mandatory reporting, and other overhead expenses associated with employees.</p>
    <p>But cost is not the only reason to outsource. Your core business is not IT; therefore outsourcing eliminates the need for your personnel to be proficient in multiple areas, i.e. building specialized skills to support your core businesses and functions as well as accumulating skills enabling them to manage, enhance and maintain the ideal IT environment.</p>
    <p>The elimination of this responsibility allows you to focus on finding and developing personnel skills directly related to your business, and not compromising your core business components.</p>
  </div>

  <div class="what-col">
    <div class="inner">
      <p class="lead">Install, customize and support all elements of IT environments</p>
      <p>We analyze your unique business requirements, determining if modifications are cost justified for your existing computing environment.</p>
      <p class="lead">Design the best combination of hardware and software for your environment</p>
      <p>We specialize in Vantix, Corelink, Lynex, Orchard, tablets and smart phones. We are able to structure each solution to the specific type of business to achieve the best returns on investment.</p>
      <p class="lead">Tailor all components of the entire IT environment</p>
      <p>Install, customize, monitor</p>
      <ul class="bullets">
        <li>desktops</li>
        <li>multiple operating systems (Panes, Orchard, Lynex, Unex)</li>
        <li>SlatePads/tablets</li>
        <li>network backbones and their components (Ethernet, fiber, routers, switches, advanced wireless)</li>
        <li>servers</li>
        <li>virtualization (thin clients/zero clients)</li>
        <li>firewalls</li>
        <li>virus/intruder detection</li>
        <li>data encryption</li>
        <li>data analysis and more</li>
      </ul>
    </div>
  </div>
</section>

</body>
</html>
```